Industry automation wholesale website

www.velturo.eu provides solutions for automation, building automation and digital signage.

Our products are rugged, reliable, energy saving and representative.

Scope of pages:
● welcome page
- scope of products
- applications, success stories and news
● category page
- short introduction
- sub categories
- product highlights
● product page
- short introduction
- about 3 to 4 pictures
- technical specifications: materials, dimensions
- price
- related products

Optional:
● contact page
- address
- contact form
● blog
- picture
- text
● logo
● favicon / apple touch icon

Conclusion:
● We need a professionally looking site
● Bright colors (e.g. white, grey, metalic colors, blue)

some pages we like:
http://www.prandek.de/
http://www.morvalix.de/

Target Market(s)

Our target market is the industrial sector
● Target audience: engineering and IT professionals

Industry/Entity Type

Building

Requirements
Must have
• ● only use free available fonts e.g. Lumara Type Library (http://www.lumaratype.com/webfonts)
Should not have
• ● sound
● flash

```html
<!DOCTYPE html>
<html lang="en">
<head>
<meta charset="utf-8">
<title>Velturo – industrial automation</title>
<link rel="stylesheet" href="https://fonts.googleapis.com/css2?family=Merriweather+Sans:wght@300;400;700&family=Open+Sans:ital,wght@0,400;0,600;1,400&display=swap">
<style>
  :root {
    --brand-blue: #1d6f94;
    --brand-deep: #0f4a68;
    --nav-top: #1f6687;
    --nav-bottom: #0e3e58;
    --search-dark: #1c2a33;
    --text: #3a3a3a;
    --muted: #555;
    --rule: #c9c9c9;
    --panel: #ffffff;
    --bg: #ffffff;
    --hero-a: #cfe3ee;
    --hero-b: #6f9fb8;
    --hero-c: #2f5f7a;
    --social: #4a79c8;
    --social-tw: #5ab7d9;
    --social-rss: #ef8a1e;
  }
  * { box-sizing: border-box; margin: 0; padding: 0; }
  html, body { width: 1200px; height: 964px; overflow: hidden; background: var(--bg); }
  body { position: relative; font-family: "Merriweather Sans", sans-serif; font-weight: 300; color: var(--text); }

  .edge-top, .edge-bottom { position: absolute; left: 0; width: 1200px; background: var(--brand-blue); }
  .edge-top { top: 0; height: 4px; }
  .edge-bottom { bottom: 0; height: 5px; }

  .brand { position: absolute; left: 126px; top: 42px; display: flex; align-items: center; gap: 12px; }
  .brand-name { font-size: 40px; font-weight: 400; color: var(--brand-blue); line-height: 1; }
  .brand-dot { width: 12px; height: 12px; border-radius: 50%; background: var(--brand-blue); }

  .contact { position: absolute; top: 19px; right: 118px; display: flex; gap: 22px; font-family: "Open Sans", sans-serif; font-size: 15px; color: var(--brand-blue); align-items: center; letter-spacing: .5px; }
  .contact span { display: flex; align-items: center; gap: 10px; }

  .language { position: absolute; left: 915px; top: 63px; width: 163px; height: 38px; border: 1px solid var(--rule); font-family: "Open Sans", sans-serif; font-style: italic; font-size: 14px; color: var(--brand-deep); padding: 9px 11px; }
  .language::after { content: ""; position: absolute; right: 10px; top: 16px; border: 6px solid transparent; border-top: 7px solid var(--brand-blue); }

  .hero { position: absolute; left: 0; top: 151px; width: 1200px; height: 245px;
    background: radial-gradient(circle at 740px 120px, rgba(255,255,255,.55) 0 60px, transparent 130px),
                radial-gradient(circle at 1140px 280px, rgba(255,255,255,.35) 0 70px, transparent 120px),
                linear-gradient(100deg, var(--hero-c) 0%, var(--hero-b) 35%, var(--hero-a) 60%, var(--hero-b) 80%, var(--hero-c) 100%); }

  .nav { position: absolute; left: 98px; top: 128px; width: 1003px; height: 47px; border: 1px solid #0a3147; background: linear-gradient(var(--nav-top), var(--nav-bottom)); display: flex; }
  .nav a { color: #fff; text-decoration: none; font-family: "Open Sans", sans-serif; font-size: 17px; line-height: 44px; position: relative; }
  .nav .home { margin-left: 47px; }
  .nav .home::after { content: ""; position: absolute; left: -12px; right: -10px; bottom: 0; height: 3px; background: #fff; }
  .nav .products { margin-left: 59px; } .nav .contact-link { margin-left: 66px; } .nav .cart { margin-left: 72px; }
  .nav-search { position: absolute; right: 0; top: 0; width: 222px; height: 45px; background: var(--search-dark); color: #e6e6e6; font-family: "Open Sans", sans-serif; font-style: italic; font-size: 13px; padding: 14px 16px; }
  .nav-search svg { position: absolute; right: 14px; top: 13px; }

  .slider-dots { position: absolute; top: 206px; left: 1001px; display: flex; gap: 9px; }
  .slider-dots i { width: 12px; height: 12px; border-radius: 50%; background: #333; }
  .slider-dots i.on { background: #fff; }

  .hero-card { position: absolute; left: 135px; top: 217px; width: 395px; height: 136px; background: #fff; padding: 14px 15px; }
  .hero-card h2 { font-size: 22px; font-weight: 700; color: var(--brand-blue); letter-spacing: .3px; margin-bottom: 12px; }
  .hero-card ul { list-style: none; font-family: "Open Sans", sans-serif; font-size: 13px; color: #222; }
  .hero-card li { display: flex; line-height: 20px; padding-left: 12px; position: relative; }
  .hero-card li::before { content: ""; position: absolute; left: 12px; top: 6px; width: 6px; height: 8px; border-radius: 3px 3px 1px 1px; background: #888; }
  .hero-card li b { font-weight: 400; width: 108px; padding-left: 18px; }

  .panel { position: absolute; left: 110px; top: 377px; width: 979px; height: 510px; background: var(--panel); box-shadow: 0 8px 14px -6px rgba(0,0,0,.25); }
  .intro { position: absolute; left: 17px; top: 38px; width: 560px; }
  h3 { font-size: 20px; font-weight: 700; color: var(--brand-blue); letter-spacing: .3px; }
  .intro p { font-size: 12.4px; line-height: 18px; width: 430px; margin: 4px 0 0 4px; color: var(--muted); }
  .intro p + p { margin-top: 18px; }
  .product-photo { position: absolute; left: 466px; top: 94px; width: 98px; height: 118px; border-radius: 8px; background: linear-gradient(135deg, #6d9bd8, #3f6eb4); }
  .features-title { font-family: "Open Sans", sans-serif; font-size: 14px; color: var(--brand-blue); margin: 6px 0 8px 3px; }
  .features { list-style: none; font-size: 12.4px; color: var(--muted); margin-left: 5px; }
  .features li { line-height: 24px; padding-left: 14px; position: relative; }
  .features li::before { content: ""; position: absolute; left: 0; top: 8px; width: 10px; height: 10px; border: 1px dotted #777; }
  .btn { display: inline-block; background: linear-gradient(#2b6d8d, #0e3f5a); color: #fff; border-radius: 5px; font-size: 13px; font-weight: 400; padding: 5px 13px; box-shadow: 0 1px 2px rgba(0,0,0,.4); }
  .more { position: absolute; left: 20px; top: 460px; }

  .sidebar { position: absolute; left: 634px; top: 38px; width: 300px; }
  .search-box { margin-top: 13px; width: 285px; height: 38px; border: 1px solid var(--rule); position: relative; }
  .search-box svg { position: absolute; right: 18px; top: 8px; }
  .advanced { position: absolute; left: 140px; top: 84px; width: 142px; height: 28px; padding: 6px 0; text-align: center; font-family: "Open Sans", sans-serif; }
  .range-title { margin-top: 64px; }
  .range { list-style: none; margin-top: 12px; font-size: 13px; color: var(--muted); }
  .range li { line-height: 30px; padding-left: 28px; position: relative; }
  .range li::before { content: ""; position: absolute; left: 4px; top: 11px; width: 8px; height: 8px; border-radius: 50%; background: var(--brand-deep); }

  .copyright { position: absolute; left: 116px; top: 905px; font-size: 12.5px; color: var(--muted); }
  .social { position: absolute; left: 893px; top: 897px; display: flex; gap: 10px; }
  .social i { width: 30px; height: 30px; border-radius: 3px; background: var(--social); box-shadow: 0 1px 2px rgba(0,0,0,.35); }
  .social i.tw { background: var(--social-tw); } .social i.rss { background: var(--social-rss); }
</style>
</head>
<body>
  <div class="edge-top"></div>

  <div class="brand"><span class="brand-name">Velturo</span><span class="brand-dot"></span></div>

  <div class="contact">
    <span>
      <svg width="14" height="22" viewBox="0 0 14 22" aria-hidden="true"><path d="M3 1h3l1 5-2 2c1 3 2 5 4 7l2-1 3 3-1 3c-4 1-12-9-12-15z" fill="#333"/></svg>
      + 49-211-5550147
    </span>
    <span>
      <svg width="22" height="18" viewBox="0 0 22 18" aria-hidden="true"><rect x="1" y="3" width="20" height="14" rx="1" fill="#8fb3cf"/><path d="M1 4l10 7 10-7" stroke="#fff" stroke-width="1.5" fill="none"/></svg>
      info@velturo.de
    </span>
  </div>

  <div class="language">Select Language</div>

  <div class="hero" role="img" aria-label="Soft blue light bokeh background"></div>

  <nav class="nav">
    <a class="home">Home</a>
    <a class="products">Products</a>
    <a class="contact-link">Contact us</a>
    <a class="cart">Shopping Cart : item(0)</a>
    <div class="nav-search">Search...
      <svg width="20" height="20" viewBox="0 0 20 20" aria-hidden="true"><circle cx="8" cy="8" r="6" stroke="#fff" stroke-width="2.5" fill="none"/><path d="M12.5 12.5l6 6" stroke="#fff" stroke-width="3"/></svg>
    </div>
  </nav>

  <div class="slider-dots"><i></i><i></i><i></i><i class="on"></i></div>

  <div class="hero-card">
    <h2>Touch Panel PC / Bedienterminal</h2>
    <ul>
      <li><b>Industrial :</b>IP65 Front . 24/7 continuous operation</li>
      <li><b>Performance :</b>Corenix Auto DualCore1.8 GHz.</li>
      <li><b>Fanless :</b>Lowheat emission, Power Saving</li>
    </ul>
  </div>

  <main class="panel">
    <section class="intro">
      <h3>RS422 / RS485 Converter</h3>
      <p style="margin-top:12px">Our VeltaDAQ RS422 / RS485 converters, RS422 / RS485 repeaters and RS485 Feldbus remote IO modules have been developed for professional use in the industry.</p>
      <p>The production line includes the converters RS232 RS422, USB RS422, RS232 RS485 and USB RS485, the repeaters RS422 and RS485, and serial IP converters.</p>
      <div class="features-title">Features:</div>
      <ul class="features">
        <li>RS422/RS485 communication: up to 1200m</li>
        <li>Extended operating temperature: -25°C to +75°C</li>
        <li>Power input: +10V to +30V</li>
        <li>Isolation between input and output signal</li>
        <li>Automatic baudrate detection (no dip-switch)</li>
        <li>automatically recognized whether a RS232 or a RS422 / RS485 Feldbus network has been connected</li>
        <li>parameters and the direction of the transmission are recognized automatically</li>
        <li>Cap-rails and wall supporters included</li>
      </ul>
    </section>
    <div class="product-photo" role="img" aria-label="Blue RS485 converter module with green terminal blocks"></div>
    <a class="btn more">more products</a>

    <aside class="sidebar">
      <h3>Product search</h3>
      <div class="search-box">
        <svg width="20" height="20" viewBox="0 0 20 20" aria-hidden="true"><circle cx="8" cy="8" r="6" stroke="#555" stroke-width="2" fill="none"/><path d="M12.5 12.5l5 5" stroke="#555" stroke-width="2.5"/></svg>
      </div>
      <a class="btn advanced">Advanced Search</a>
      <h3 class="range-title">Range of products</h3>
      <ul class="range">
        <li>RS422 / RS485 Converter</li>
        <li>RS422 / RS485 Repeater</li>
        <li>RS485 Remote IO</li>
        <li>RS485 Modbus IO</li>
        <li>Embedded Systems</li>
        <li>PCI-Series</li>
        <li>Industry PC</li>
        <li>Industrial Display</li>
        <li>Din Rail Power Supply</li>
      </ul>
    </aside>
  </main>

  <footer>
    <div class="copyright">© 2014. www.companyname.com</div>
    <div class="social" aria-label="Social links"><i></i><i class="tw"></i><i class="rss"></i><i></i></div>
  </footer>

  <div class="edge-bottom"></div>
</body>
</html>
```